Need CATCHY/VIVID Banner design for my new UTV/ATV/Off Road Vehicle turn signal/lighting company

I need a banner ad designed so I can advertise on several different ATV (all terrain vehicle), UTV (Utility Vehicles), Golf Cart and Off-Road Vehicle forums. Ads need to be very catchy and produce a call to action. Action is getting hits to my website. Our main business is selling turn signal kits to make your side by side or your ATV/UTV street legal, as some states now allow you to drive these on public roads if you have the following items: Turn Signals, Horn, Lighted license plate bracket, headlights and brake lights. We sell all of these items for just about any model vehicle out there. Our call to action for this banner would be to get more website visits.

Target Market(s)

Off-road/outdoor enthusiasts,

Industry/Entity Type

Car Accessorie

Font styles to use
Sans Serif

Requirements
Must have
• Ad size need to be either 728x90 or 300x250. Colorful ad with an off-road vehicle integrated to the design (think UTV, side-by-side, etc.
Nice to have
• Nice to haves would be anything that makes this banner ad stand out on very boring web pages.
Should not have
• anything dull

```html
<!DOCTYPE html>
<html lang="en">
<head>
<meta charset="utf-8">
<title>Trailwink – ATV Signal Lighting Banner</title>
<link rel="stylesheet" href="https://fonts.googleapis.com/css2?family=Barlow+Semi+Condensed:wght@500;600;700&display=swap">
<style>
  :root {
    --ink-dark: #160707;
    --red-deep: #5a0a0e;
    --red: #c3121b;
    --red-bright: #e01b22;
    --yellow: #ffc20e;
    --orange: #f58a12;
    --white: #ffffff;
    --sky: #b9c4cc;
    --sand: #b88a5a;
    --rock: #7a5a40;
  }
  * { margin: 0; padding: 0; box-sizing: border-box; }
  html, body { width: 1200px; height: 1000px; overflow: hidden; background: var(--ink-dark); }
  .banner {
    position: relative;
    width: 1200px;
    height: 1000px;
    overflow: hidden;
    font-family: "Barlow Semi Condensed", "Arial Narrow", sans-serif;
    color: var(--white);
  }
  .hero-photo {
    position: absolute;
    inset: 0;
    background:
      linear-gradient(180deg, var(--sky) 0%, #d8cfc2 22%, var(--sand) 48%, var(--rock) 78%, #4a3426 100%);
  }
  .shapes { position: absolute; inset: 0; }
  .brand {
    position: absolute;
    left: 40px;
    top: 50px;
    display: flex;
    align-items: center;
    gap: 16px;
    font-weight: 700;
    font-size: 64px;
    letter-spacing: 2px;
    color: var(--yellow);
    line-height: 1;
  }
  .brand-dot { width: 30px; height: 30px; background: var(--red-bright); border-radius: 50%; }
  .tagline {
    position: absolute;
    left: 32px;
    top: 196px;
    font-weight: 700;
    text-transform: uppercase;
    line-height: 1.05;
  }
  .tagline .main { font-size: 42px; letter-spacing: 0.5px; }
  .tagline .sub { font-size: 31px; letter-spacing: 0.5px; }
  .headline {
    position: absolute;
    left: 36px;
    top: 336px;
    font-weight: 600;
    text-transform: uppercase;
    line-height: 1.04;
  }
  .headline .accent { display: block; font-size: 68px; color: var(--yellow); }
  .headline .plain { display: block; font-size: 62px; }
  .feature-icons {
    position: absolute;
    left: 36px;
    top: 508px;
    display: flex;
    gap: 40px;
    align-items: center;
  }
  .feature-icons svg { height: 54px; }
  .vehicle-photo {
    position: absolute;
    left: 30px;
    top: 600px;
    width: 450px;
    height: 370px;
    border-radius: 40px 40px 30px 30px;
    background: radial-gradient(ellipse at 50% 55%, #e2e0dc 0%, #9b9a98 45%, #c24a2a 70%, rgba(195,18,27,0) 78%);
  }
</style>
</head>
<body>
<div class="banner">
  <div class="hero-photo" role="img" aria-label="Photo of a red and black side-by-side UTV climbing rocks in a desert with mountains behind"></div>

  <svg class="shapes" viewBox="0 0 1200 1000" aria-hidden="true">
    <defs>
      <linearGradient id="panel-fill" x1="0" y1="0" x2="0" y2="1">
        <stop offset="0" stop-color="var(--ink-dark)"/>
        <stop offset="0.4" stop-color="var(--red-deep)"/>
        <stop offset="1" stop-color="var(--red-bright)"/>
      </linearGradient>
      <linearGradient id="stripe-fill" x1="0" y1="0" x2="0" y2="1">
        <stop offset="0" stop-color="var(--yellow)"/>
        <stop offset="0.55" stop-color="var(--orange)"/>
        <stop offset="1" stop-color="var(--yellow)"/>
      </linearGradient>
    </defs>
    <polygon points="820,0 880,0 630,580 1000,1000 940,1000 570,580" fill="url(#stripe-fill)"/>
    <polygon points="0,0 820,0 570,580 940,1000 0,1000" fill="url(#panel-fill)"/>
    <polygon points="760,0 820,0 570,580 940,1000 880,1000 540,600" fill="var(--red)" opacity="0.85"/>
  </svg>

  <div class="brand"><span class="brand-dot"></span>TRAILWINK</div>

  <div class="tagline">
    <div class="main">Turn Signal Kits</div>
    <div class="sub">&amp; Lighting Accessories</div>
  </div>

  <h1 class="headline">
    <span class="accent">ATV Vechicle</span>
    <span class="plain">Signal Lighting</span>
  </h1>

  <div class="feature-icons">
    <svg viewBox="0 0 60 54" aria-label="Brake light">
      <circle cx="30" cy="27" r="17" fill="none" stroke="#fff" stroke-width="4"/>
      <path d="M10 8 A26 26 0 0 0 10 46 M50 8 A26 26 0 0 1 50 46" fill="none" stroke="#fff" stroke-width="4"/>
      <rect x="27.5" y="15" width="5" height="15" fill="#fff"/>
      <circle cx="30" cy="36" r="3" fill="#fff"/>
    </svg>
    <svg viewBox="0 0 70 54" aria-label="Headlight">
      <path d="M38 8 C58 8 62 46 38 46 Z" fill="#fff"/>
      <g stroke="#fff" stroke-width="4"><line x1="6" y1="14" x2="28" y2="14"/><line x1="6" y1="27" x2="28" y2="27"/><line x1="6" y1="40" x2="28" y2="40"/></g>
    </svg>
    <svg viewBox="0 0 90 54" aria-label="Horn">
      <g stroke="#fff" stroke-width="3"><line x1="4" y1="14" x2="12" y2="20"/><line x1="2" y1="27" x2="12" y2="27"/><line x1="4" y1="40" x2="12" y2="34"/></g>
      <path d="M18 22 L60 22 L84 8 L84 46 L60 32 L18 32 Z" fill="none" stroke="#fff" stroke-width="3.5" stroke-linejoin="round"/>
      <rect x="24" y="32" width="6" height="8" fill="#fff"/>
    </svg>
    <svg viewBox="0 0 84 54" aria-label="Turn signals">
      <path d="M4 27 L24 8 L24 18 L36 18 L36 36 L24 36 L24 46 Z" fill="none" stroke="#fff" stroke-width="3.5" stroke-linejoin="round"/>
      <path d="M80 27 L60 8 L60 18 L48 18 L48 36 L60 36 L60 46 Z" fill="none" stroke="#fff" stroke-width="3.5" stroke-linejoin="round"/>
    </svg>
  </div>

  <div class="vehicle-photo" role="img" aria-label="Photo of a grey and orange sport side-by-side UTV with roll cage"></div>
</div>
</body>
</html>
```